Ridgeline Journeys business card

please see website
www.ridgelinejourneys.comau

info needed on card
Curtis Halvey
Ph
email
Adventure Riding GPS trails

please use my logo and colours off my site

Curtis Halvey
curtis@ridgelinejourneys.com

```html
<!DOCTYPE html>
<html lang="en">
<head>
<meta charset="utf-8">
<title>Ridgeline Journeys – Business Card</title>
<link rel="stylesheet" href="https://fonts.googleapis.com/css2?family=Source+Sans+3:ital,wght@0,400;0,600;0,700;1,400;1,600&display=swap">
<style>
  :root {
    --backdrop: #4a4a4a;
    --card-white: #f6f6f6;
    --card-black: #050505;
    --brand-yellow: #f5d400;
    --brand-yellow-deep: #eebf00;
    --ink: #111111;
    --paper-text: #ffffff;
    --mark-grey: #5f5f5f;
  }
  * { margin: 0; padding: 0; box-sizing: border-box; }
  html, body {
    width: 1200px; height: 750px; overflow: hidden;
    background: var(--backdrop);
    font-family: "Source Sans 3", sans-serif;
  }
  .card {
    position: absolute;
    left: 371px;
    width: 461px;
    height: 263px;
    overflow: hidden;
    box-shadow: 0 3px 8px rgba(0,0,0,0.45);
  }
  .card--front { top: 99px; background: var(--card-white); }
  .card--back { top: 381px; background: var(--card-black); }

  .front-wave { position: absolute; inset: 0; width: 100%; height: 100%; }

  .brand {
    position: absolute;
    display: flex;
    align-items: center;
    gap: 12px;
  }
  .brand__dot {
    border-radius: 50%;
    background: var(--brand-yellow);
    flex: none;
  }
  .brand__name {
    font-weight: 700;
    color: var(--ink);
    text-transform: uppercase;
    line-height: 0.95;
  }
  .card--front .brand { left: 30px; top: 34px; }
  .card--front .brand__dot { width: 50px; height: 50px; }
  .card--front .brand__name { font-size: 22px; }

  .contact {
    position: absolute;
    right: 26px;
    top: 136px;
    text-align: right;
    color: var(--paper-text);
  }
  .contact__name {
    font-size: 17.5px;
    font-weight: 600;
    color: var(--brand-yellow);
    margin-bottom: 9px;
  }
  .contact__list { list-style: none; }
  .contact__item {
    display: flex;
    justify-content: flex-end;
    align-items: center;
    gap: 7px;
    font-size: 11px;
    height: 17.5px;
  }
  .contact__icon { width: 11px; height: 11px; flex: none; }
  .contact__tagline {
    margin-top: 5px;
    font-size: 13px;
    font-style: italic;
    font-weight: 600;
  }

  .card--back .brand {
    left: 0; right: 0; top: 70px;
    flex-direction: column;
    gap: 14px;
  }
  .card--back .brand__dot { width: 72px; height: 72px; }
  .card--back .brand__name { color: var(--paper-text); font-size: 22px; letter-spacing: 0.5px; }
  .back-url {
    position: absolute;
    left: 0; right: 0; top: 216px;
    text-align: center;
    font-size: 11px;
    font-style: italic;
    color: var(--brand-yellow);
  }
</style>
</head>
<body>

<section class="card card--front">
  <svg class="front-wave" viewBox="0 0 576 329" preserveAspectRatio="none" aria-hidden="true">
    <path fill="var(--brand-yellow)" d="M0,231 C70,290 180,300 280,240 C360,190 410,100 500,78 C540,70 560,72 576,80 L576,329 L0,329 Z"/>
    <path fill="var(--card-black)" stroke="#ffffff" stroke-width="3" d="M0,256 C60,300 130,310 200,295 C290,275 370,160 440,110 C480,82 530,70 576,86 L578,331 L-2,331 Z"/>
  </svg>

  <div class="brand">
    <span class="brand__dot"></span>
    <span class="brand__name">Ridgeline<br>Journeys</span>
  </div>

  <div class="contact">
    <p class="contact__name">Curtis Halvey</p>
    <ul class="contact__list">
      <li class="contact__item">612 555 0148
        <svg class="contact__icon" viewBox="0 0 24 24" aria-hidden="true"><path fill="var(--brand-yellow)" d="M6.6 10.8a15.1 15.1 0 0 0 6.6 6.6l2.2-2.2a1 1 0 0 1 1-.25 11.4 11.4 0 0 0 3.6.57 1 1 0 0 1 1 1V20a1 1 0 0 1-1 1A17 17 0 0 1 3 4a1 1 0 0 1 1-1h3.5a1 1 0 0 1 1 1c0 1.25.2 2.45.57 3.57a1 1 0 0 1-.25 1z"/></svg>
      </li>
      <li class="contact__item">curtis@ridgelinejourneys.com
        <svg class="contact__icon" viewBox="0 0 24 24" aria-hidden="true"><rect x="1" y="5" width="22" height="14" fill="var(--brand-yellow)"/><path d="M1 5 L12 13 L23 5" fill="none" stroke="var(--card-black)" stroke-width="2"/></svg>
      </li>
      <li class="contact__item">www.ridgelinejourneys.com.au
        <svg class="contact__icon" viewBox="0 0 24 24" aria-hidden="true"><circle cx="12" cy="12" r="11" fill="var(--brand-yellow)"/><path d="M12 1a11 11 0 0 0 0 22M1 12h22M12 1c-4 4-4 18 0 22" fill="none" stroke="var(--card-black)" stroke-width="1.6"/></svg>
      </li>
    </ul>
    <p class="contact__tagline">Adventure Riding GPS trails</p>
  </div>
</section>

<section class="card card--back">
  <div class="brand">
    <span class="brand__dot"></span>
    <span class="brand__name">Ridgeline Journeys</span>
  </div>
  <p class="back-url">www.ridgelinejourneys.com.au</p>
</section>

</body>
</html>
```